To design a brand identity that is simple and creative with 'Corvane' as the brand name, I like modern simple fonts like helvetica neue, I want to print both sides of the card, I am open to dark front and white back, but the design needs to transfer well to letter heads and email signatures, I am looking for sophisticated and elegant, but open minded about clever and off the wall, I do not do 'boring' Corvane Ventures is the mother company for a small group, specialising in Management & consulting, Software development and construction, we have a high level of integrity, we are transparent and accountable for what we do. my images are provided as a guide only, Im not expecting them to be just copied, Im looking for a creator and passionate thinker, who will put life into their work.

Target Market(s)

usually business minded people who are looking for something different in me, such as leadership, confidence and focus with thinking that is per haps a little outside the box..

Industry/Entity Type

Construction

Requirements
Must have
• clean, minmalistic
Nice to have
• custom logo
Should not have
• boring, traditional

```html
<!DOCTYPE html>
<html lang="en">
<head>
<meta charset="utf-8">
<title>Corvane — Business Card</title>
<link href="https://fonts.googleapis.com/css2?family=Quicksand:wght@400;500;700&display=swap" rel="stylesheet">
<style>
  :root {
    --backdrop: #3a3a3b;
    --card: #353536;
    --brand-orange: #e0743a;
    --text-light: #d9d9d9;
    --text-muted: #a9a9aa;
    --rule: #5a5a5b;
    --purple: #8e5aa8;
    --pink: #d6476b;
    --yellow: #f2bf3a;
    --teal: #2f9a88;
  }
  * { margin: 0; padding: 0; box-sizing: border-box; }
  html, body { width: 1200px; height: 848px; overflow: hidden; }
  body {
    background: radial-gradient(ellipse at 20% 20%, #4a4a4b 0%, var(--backdrop) 60%, #2e2e2f 100%);
    font-family: "Quicksand", "Helvetica Neue", Arial, sans-serif;
    position: relative;
  }
  .card {
    position: absolute;
    top: 130px;
    width: 380px;
    height: 588px;
    background: var(--card);
    overflow: hidden;
    box-shadow: 0 18px 40px rgba(0,0,0,0.45);
  }
  .card--front { left: 170px; }
  .card--back { left: 650px; }

  .colour-field {
    position: absolute;
    top: 0;
    left: 0;
    width: 100%;
    background:
      linear-gradient(to bottom, rgba(53,53,54,0) 55%, var(--card) 100%),
      linear-gradient(to right, var(--purple), var(--pink) 35%, var(--yellow) 65%, var(--teal));
    opacity: 0.85;
  }
  .card--front .colour-field { height: 330px; }
  .card--back .colour-field { height: 190px; }

  .brand { position: absolute; display: flex; align-items: center; gap: 12px; }
  .brand__dot { border-radius: 50%; background: var(--brand-orange); flex: none; }
  .brand__name {
    display: block;
    color: var(--brand-orange);
    font-weight: 500;
    line-height: 1;
    letter-spacing: 1px;
  }
  .brand__tagline {
    display: block;
    color: var(--text-muted);
    font-weight: 400;
    letter-spacing: 0.5px;
    margin-top: 6px;
  }
  .card--front .brand { left: 30px; bottom: 78px; }
  .card--front .brand__dot { width: 44px; height: 44px; }
  .card--front .brand__name { font-size: 50px; }
  .card--front .brand__tagline { font-size: 12px; }
  .card--back .brand { left: 178px; top: 222px; gap: 9px; }
  .card--back .brand__dot { width: 30px; height: 30px; }
  .card--back .brand__name { font-size: 32px; }
  .card--back .brand__tagline { font-size: 10px; }

  .contact {
    position: absolute;
    left: 36px;
    right: 30px;
    top: 392px;
    color: var(--text-light);
    font-size: 17px;
    line-height: 1.3;
  }
  .contact__email { font-weight: 700; font-size: 19px; }
  .contact__role { margin-bottom: 10px; }
  .contact__address { display: flex; align-items: center; gap: 6px; }
  .contact__address svg { width: 10px; height: 15px; flex: none; }
  .contact__phone { padding-left: 50px; }
  .contact__rule { border: 0; border-top: 1px solid var(--rule); margin: 12px 0; }
  .contact__services { font-size: 16px; letter-spacing: 0.5px; }
</style>
</head>
<body>

<section class="card card--front" aria-label="Card front">
  <div class="colour-field" role="img" aria-label="Decorative band of coloured vertical stripes in purple, pink, yellow and teal"></div>
  <div class="brand">
    <span class="brand__dot"></span>
    <div>
      <span class="brand__name">corvane</span>
      <span class="brand__tagline">built with clear intent</span>
    </div>
  </div>
</section>

<section class="card card--back" aria-label="Card back">
  <div class="colour-field" role="img" aria-label="Decorative band of coloured vertical stripes in purple, pink, yellow and teal"></div>
  <div class="brand">
    <span class="brand__dot"></span>
    <div>
      <span class="brand__name">corvane</span>
      <span class="brand__tagline">built with clear intent</span>
    </div>
  </div>
  <div class="contact">
    <div class="contact__email">ruth@corvane.ventures</div>
    <div class="contact__role">Client Ambassador</div>
    <div class="contact__address">
      <svg viewBox="0 0 10 15" aria-hidden="true"><rect x="0.75" y="0.75" width="8.5" height="13.5" rx="1.5" fill="none" stroke="#d9d9d9" stroke-width="1.2"/><line x1="3.5" y1="12" x2="6.5" y2="12" stroke="#d9d9d9" stroke-width="1"/></svg>
      <span>Po Box 418 Harlow 5120</span>
    </div>
    <div class="contact__phone">+61 040 555 019</div>
    <hr class="contact__rule">
    <div class="contact__services">Management. software. construction</div>
    <hr class="contact__rule">
  </div>
</section>

</body>
</html>
```